Stationery Design Project

We need a stationery design for our Norwegian trucking company. We have existed for about 15 years and our 12 drivers uses relatively new vehicles to transport goods around in northern Norway. Long distance routes with fresh fish og food transport is our main operations.

We have already made alogo that's printed on our trucks. The logo and a picture of our trucks is attached. I think the logo i crappy, but since its already in use, changing it is not an option in this round. Still using a better colour scheme in the overall stationery and more interesting fonts is possible (altso in the logo).

Company details:
Name: Kjelvraket AS
Organisation nr 873 615 309
Post adress: 8642 Raudvik

I like minimalism and simplicity. I am avalibly for questions in normal GMT working hours either here or on mail: ivar@fjordlast.no

Reason: Hi. Im extending the deadline because I needed some time to find a vector file of our logo. Sorry for the inconvenience

Hi, and thanks for all your interest in the project. Some updates:

-          I have decided to commit to using one of the designs. Some designer will get the payment.

-          I have extended the deadline with 24 hours since I needed some time to find our firms vector logo (a slow Swedish man was holding me up)

-          We will not choose a design before the deadline. No need to rush.

-          We have received a lot of great design and think there is a need to specified the product we want to make:

o   Business Card for all our employers. I just need the design and will duplicate with the correct numbers and name myself. The information on should be: Logo, employer’s name, Phone number, email, website, Postal number and address. Use this as a template: logo, Leif Brattvoll, 47382066, Leif@fjordlast.no,, fjordlast.no, 8642 Raudvik. The order and placement of the information is your creative decision.

o   Stickers to put on the goods we travel. On the sticker the should be the following information: Logo, phone number, Tekst and link: Fraktæ av Kjelvraket. Ke du syns? Fjordlast.no/tilbakemelding (this means: Handled by Kjelvraket. What do you think Fjordlast.no/feedback -à the link will be a feedback form). The placement the information and size is your creative decision with some stings: we have been thinking of using Drukko for printing and see that a size about 6x6 cm, 8x5 or something like that. (with 3000 copies our budget is 200 punds). Any suggestions of other suppliers are welcome. Drukko price calculator http://www.drukkolabelhouse.co.uk/digital-litho-printing/printing-labels-tags/stickers/

o   Letterhead with logo, address, phone number and organizational number.

o   Envelopes with logo,address, phone number and organizational number.

Have a nice day.

 

 

• Using the blue colour in the logo and using a similar graphic approch.

```html
<!DOCTYPE html>
<html lang="no">
<head>
<meta charset="utf-8">
<title>Kjelvraket AS – Stationery</title>
<link rel="stylesheet" href="https://fonts.googleapis.com/css2?family=PT+Serif:ital,wght@0,400;0,700;1,400&display=swap">
<style>
  :root {
    --backdrop: #cbcbcb;
    --paper: #ffffff;
    --navy: #0b0087;
    --royal: #2955d4;
    --ink-soft: #eef1ff;
  }
  html, body {
    margin: 0;
    padding: 0;
    width: 1200px;
    height: 1000px;
    overflow: hidden;
    background: var(--backdrop);
    font-family: "PT Serif", Georgia, serif;
  }
  .canvas { position: relative; width: 1200px; height: 1000px; }

  .sheet {
    position: absolute;
    background: var(--paper);
    overflow: hidden;
    border: 1px solid #8a8a8a;
    box-sizing: border-box;
  }
  .sheet .swoosh { position: absolute; inset: 0; width: 100%; height: 100%; }

  .brand {
    position: absolute;
    display: flex;
    align-items: center;
    gap: 6px;
    font-weight: 700;
    color: var(--royal);
    line-height: 1;
  }
  .brand .brand-dot {
    width: 0.7em;
    height: 0.7em;
    border-radius: 50%;
    background: var(--navy);
  }

  /* Letterhead */
  .letterhead { left: 50px; top: 184px; width: 490px; height: 692px; }
  .letterhead .brand { left: 36px; top: 42px; font-size: 24px; }
  .letterhead .footer-line {
    position: absolute;
    left: 0; right: 0;
    bottom: 12px;
    text-align: center;
    font-style: italic;
    font-size: 8px;
    color: var(--ink-soft);
    padding-left: 0;
  }

  /* Business card back */
  .card-back { left: 694px; top: 196px; width: 312px; height: 178px; background: var(--navy); border-color: var(--navy); }
  .card-back .brand { left: 0; right: 0; top: 72px; justify-content: center; font-size: 22px; }
  .card-back .brand .brand-dot { background: var(--royal); }

  /* Business card front */
  .card-front { left: 694px; top: 396px; width: 312px; height: 178px; }
  .card-front .brand { left: 28px; top: 28px; font-size: 17px; }
  .card-front .holder {
    position: absolute;
    left: 30px; top: 85px;
    font-size: 8.5px;
    letter-spacing: 2px;
    color: var(--navy);
  }
  .card-front .role {
    position: absolute;
    left: 141px; top: 86px;
    font-size: 7px;
    font-style: italic;
    letter-spacing: 1px;
    color: var(--navy);
  }
  .card-front .contacts {
    position: absolute;
    left: 120px; top: 101px;
    margin: 0;
    display: grid;
    grid-template-columns: 18px auto;
    column-gap: 3px;
    row-gap: 0;
    font-size: 6.5px;
    line-height: 8.5px;
  }
  .card-front .contacts dt { text-align: right; font-weight: 700; color: #111; }
  .card-front .contacts dd { margin: 0; font-style: italic; letter-spacing: 1px; color: var(--navy); }

  /* Envelope */
  .envelope { left: 590px; top: 644px; width: 559px; height: 237px; }
  .envelope .brand { left: 28px; top: 30px; font-size: 22px; }
</style>
</head>
<body>
<main class="canvas">

  <section class="sheet letterhead" aria-label="Letterhead">
    <div class="brand"><span class="brand-dot"></span>Kjelvraket</div>
    <svg class="swoosh" viewBox="0 0 490 692" preserveAspectRatio="none" aria-hidden="true">
      <path d="M110 656 Q380 648 490 564 L490 588 Q360 655 110 656 Z" fill="var(--navy)"/>
      <path d="M0 655 Q300 672 490 598 L490 692 L0 692 Z" fill="var(--royal)"/>
    </svg>
    <p class="footer-line">Kjelvraket AS, Organisation NR 873 615 309 8642 Raudvik</p>
  </section>

  <section class="sheet card-back" aria-label="Business card, reverse">
    <svg class="swoosh" viewBox="0 0 312 178" preserveAspectRatio="none" aria-hidden="true">
      <path d="M0 150 Q200 178 312 150 L312 178 L0 178 Z" fill="var(--royal)"/>
    </svg>
    <div class="brand"><span class="brand-dot"></span>Kjelvraket</div>
  </section>

  <section class="sheet card-front" aria-label="Business card, front">
    <div class="brand"><span class="brand-dot"></span>Kjelvraket</div>
    <p class="holder">KJELVRAKET</p>
    <p class="role">Mktng. Director</p>
    <dl class="contacts">
      <dt>p:</dt><dd>+47 063 41200</dd>
      <dt>m:</dt><dd>+47 063 41200</dd>
      <dt>e:</dt><dd>ivar@fjordlast.no</dd>
      <dt>w:</dt><dd>www.kjelvraket.no</dd>
    </dl>
    <svg class="swoosh" viewBox="0 0 312 178" preserveAspectRatio="none" aria-hidden="true">
      <path d="M20 177 Q240 168 312 126 L312 136 Q250 172 20 177 Z" fill="var(--royal)"/>
      <path d="M0 178 Q220 173 312 148 L312 178 Z" fill="var(--navy)"/>
    </svg>
  </section>

  <section class="sheet envelope" aria-label="Envelope">
    <div class="brand"><span class="brand-dot"></span>Kjelvraket</div>
    <svg class="swoosh" viewBox="0 0 559 237" preserveAspectRatio="none" aria-hidden="true">
      <path d="M128 202 Q430 194 559 108 L559 130 Q420 200 128 202 Z" fill="var(--navy)"/>
      <path d="M0 201 Q320 216 559 140 L559 237 L0 237 Z" fill="var(--royal)"/>
    </svg>
  </section>

</main>
</body>
</html>
```